KTR Photography Editing & Support Services for Real Estate

We require a double sided A4 flyer to promote our photography services to real estate agencies.
This particular service is targeted to rural areas where reliable, professional and highly skilled photographers are difficult to source. We teach the agent how to photograph, they upload files to a server and we take care of the rest (image editing, quality control and delivery). This will give the agents flexibility with when to shoot and eliminates the stress of managing a photographer / contractor. We offer a 1 day face to face training session and competitive packages for equipment start up.
We would like the flyer to look clean & very professional. The flyer should showcase samples of our work to highlight what can be achieved by using our services. We like the look of a black or dark background behind the text and feel that would look nice with our photographs provided. Otherwise open to your suggestions and ideas.
TEXT FOR FLYER:
Welcome to the KTR Real Estate Photography Editing and Support Service
• Take your real estate business to the next level by providing impressive real estate imagery that makes you stands out from the competition
• Omit the stress of trying to find a good photographer or managing an unreliable one and hence have more time to focus on other aspects of your business
• Showcase your listings with better quality and more impactful photographs than your competitors thereby increasing potential for a quick sale
• Great first impressions matter and you will achieve this by looking and feeling more professional. This will attract and retain more future clients.
HOW IT WORKS
• We understand that your time is valuable, so let us handle the editing and delivery of your images. You shoot, and we take care of the rest.
• Images are edited and delivered within 1 working day
INCLUSIONS:
• Full day face to face training (we come to you) and instructional handbook
• We will teach you everything you need to know about your equipment and how to take stunning real estate photographs
• Service turnaround within 1 working day
• Free HELP desk service Mon-Fri
• 12 month Exclusivity (rural towns only) for a limited time
INVESTMENT
• 99 per listing for us to manage images including editing, quality control and delivery (10 Images)
• Ask us about competitive packages for photography equipment if required
SUMMARY
The KTR Real Estate Photography Editing and Support Service is the perfect solution for busy real estate professionals who want to take their business to the next level. Our service is affordable, flexible, and designed to help you showcase your listings in the best possible light.
Contact us today to learn more about how we can help you.

```html
<!DOCTYPE html>
<html lang="en">
<head>
<meta charset="utf-8">
<title>KTR Real Estate Photography – Editing and Support Service Flyer</title>
<link rel="stylesheet" href="https://fonts.googleapis.com/css2?family=Poppins:wght@300;400;500;600;700;800&family=Great+Vibes&display=swap">
<style>
:root{
  --ink:#111111;
  --band:#0b0b0b;
  --panel:#222222;
  --panel-head:#141414;
  --grey:#8b8b8b;
  --grey-dark:#6a6a6a;
  --muted:#4a4a4a;
  --paper:#ffffff;
  --stage:#676767;
}
*{box-sizing:border-box;margin:0;padding:0}
html,body{width:1200px;height:3794px;overflow:hidden}
body{position:relative;background:var(--paper);font-family:"Poppins",sans-serif;color:var(--ink)}

.stage{position:absolute;left:0;top:0;width:1200px;height:863px;background:linear-gradient(160deg,#7a7a7a 0%,var(--stage) 55%,#5a5a5a 100%)}
.thumb{position:absolute;top:106px;transform:scale(.51);transform-origin:0 0}
.thumb--front{left:59px}
.thumb--back{left:638px}
.sheet{position:absolute;left:97px}
.sheet--front{top:998px}
.sheet--back{top:2392px}

.flyer{position:relative;width:981px;height:1269px;background:var(--paper);box-shadow:0 6px 22px rgba(0,0,0,.28);overflow:hidden}
.flyer > *{position:absolute}
.photo{background:linear-gradient(160deg,#8fa3b8,#4a4f55 60%,#6f7a4a)}

/* brand */
.brand{left:40px;width:370px;text-align:center;color:#3d3d3d}
.brand-name{font-size:28px;font-weight:300;letter-spacing:6px;line-height:1}
.brand-role{font-size:13px;font-weight:400;letter-spacing:4px;margin-top:14px}

/* front */
.accent-top{left:486px;top:0;width:495px;height:24px;background:var(--grey)}
.accent-side{left:940px;top:24px;width:41px;height:406px;background:var(--grey)}
.hero-frame{left:429px;top:25px;width:521px;height:425px;background:var(--paper)}
.hero-photo{left:438px;top:35px;width:502px;height:405px;background:linear-gradient(180deg,#6f87a6 0%,#a9b6c4 35%,#3a3a3e 60%,#5f6b3e 85%,#7c8a4b 100%)}
.welcome{left:62px;top:188px;font-family:"Great Vibes",cursive;font-size:60px;color:#555;line-height:1}
.title-big{left:60px;top:254px;font-size:88px;font-weight:800;line-height:1;letter-spacing:1px}
.title-sub{left:62px;top:346px;font-size:37px;font-weight:800;line-height:1.02}
.black-band{left:0;top:427px;width:981px;height:114px;background:var(--band)}
.band-text{left:62px;top:443px;color:#fff;font-size:37px;font-weight:600;line-height:1.08}
.accent-right{left:905px;top:641px;width:76px;height:280px;background:var(--grey)}
.gallery-frame{left:533px;top:472px;width:374px;height:665px;background:var(--paper)}
.g1{left:542px;top:482px;width:356px;height:206px;background:linear-gradient(180deg,#6b8fc0,#c9c4b5 55%,#8a7b62)}
.g2{left:542px;top:699px;width:356px;height:207px;background:linear-gradient(180deg,#8a6440,#274a7a 40%,#3b3a38 80%,#6b5a48)}
.g3{left:542px;top:915px;width:356px;height:211px;background:linear-gradient(90deg,#5e4a36,#d9d6d0 50%,#b8b2a8)}

.benefits{left:62px;top:566px;width:450px;list-style:none}
.benefits li{display:flex;gap:22px;margin-bottom:18px;font-size:15px;line-height:19px;color:#1e1e1e}
.icon{flex:0 0 44px;width:44px;height:44px;background:var(--grey-dark);display:flex;align-items:center;justify-content:center}
.icon svg{width:28px;height:28px}

.how-head{left:65px;top:906px;width:412px;height:47px;background:var(--grey);color:#fff;font-size:27px;font-weight:600;padding:4px 0 0 16px;letter-spacing:.5px}
.how-box{left:65px;top:953px;width:412px;height:163px;background:var(--band);padding:18px 16px 0 14px;list-style:none}
.how-box li{display:flex;gap:18px;color:#fff;font-size:16px;line-height:17px;margin-bottom:22px}
.num{flex:0 0 30px;width:30px;height:30px;border:2px solid #fff;border-radius:50%;font-size:14px;font-weight:700;display:flex;align-items:center;justify-content:center;margin-top:4px}

/* footer */
.foot-grey{left:0;width:477px;height:77px;background:var(--grey)}
.foot-black{left:477px;width:504px;height:77px;background:var(--band)}
.portrait{left:58px;width:114px;height:114px;border-radius:50%;border:5px solid #fff;background:radial-gradient(circle at 50% 40%,#7a7a7a,#2a2a2a)}
.foot-name{left:204px;color:#fff;font-size:28px;font-weight:700;line-height:32px;white-space:nowrap}
.foot-contact{left:509px;color:#fff}
.foot-contact p{display:flex;align-items:center;gap:14px;white-space:nowrap}
.foot-contact .phone{font-size:32px;font-weight:500;line-height:34px}
.foot-contact .mail{font-size:24px;font-weight:400;line-height:28px}
.cicon{width:22px;height:22px;flex:0 0 22px}
.sheet--front .foot-grey,.sheet--front .foot-black,.thumb--front .foot-grey,.thumb--front .foot-black{top:1151px}
.sheet--front .portrait,.thumb--front .portrait{top:1133px}
.sheet--front .foot-name,.thumb--front .foot-name{top:1158px}
.sheet--front .foot-contact,.thumb--front .foot-contact{top:1158px}
.sheet--back .foot-grey,.sheet--back .foot-black,.thumb--back .foot-grey,.thumb--back .foot-black{top:1156px}
.sheet--back .portrait,.thumb--back .portrait{top:1138px}
.sheet--back .foot-name,.thumb--back .foot-name{top:1163px}
.sheet--back .foot-contact,.thumb--back .foot-contact{top:1163px}

/* back */
.back-hero{left:29px;top:26px;width:921px;height:383px;background:linear-gradient(180deg,#93a8c4 0%,#c6c3cc 35%,#e7c9bd 52%,#6e7f92 60%,#8b7a5c 80%,#4e6a3e 100%)}
.back-brand{top:130px}
.inc-head{left:50px;top:387px;width:464px;height:91px;background:var(--panel-head);color:#fff;font-size:34px;font-weight:600;padding:26px 0 0 40px;letter-spacing:.5px}
.inc-body{left:50px;top:478px;width:449px;height:417px;background:var(--panel);list-style:none;padding:36px 20px 0 37px}
.inc-body li{display:flex;gap:15px;color:#fff;font-size:15px;line-height:18px;margin-bottom:26px;align-items:center}
.inc-body .icon{background:#777}
.inc-body .strong{font-size:21px;line-height:24px;font-weight:600}
.inc-body small{display:block;font-size:15px;font-weight:400;line-height:16px}
.b1{left:524px;top:423px;width:411px;height:210px;background:linear-gradient(180deg,#f4f3f0,#cfc6b8 60%,#8c7358)}
.b2{left:524px;top:648px;width:411px;height:243px;background:linear-gradient(160deg,#2c3138,#4a5058 50%,#1e1f22)}
.b3{left:524px;top:906px;width:411px;height:224px;background:linear-gradient(180deg,#e9e6e0,#9aa69a 50%,#d8d2c8)}
.inv-title{left:72px;top:925px;font-size:30px;font-weight:600;letter-spacing:.5px}
.inv-list{left:79px;top:986px;width:420px;list-style:none}
.inv-list li{display:flex;gap:14px;font-size:15px;line-height:18px;margin-bottom:24px}
.inv-list b{font-weight:600}
.tick{flex:0 0 17px;width:17px;height:17px;margin-top:1px}
</style>
</head>
<body>

<section class="stage" aria-label="Flyer front and back overview">
  <div class="thumb thumb--front">
    <article class="flyer">
      <div class="accent-top"></div><div class="accent-side"></div><div class="hero-frame"></div>
      <div class="hero-photo photo" role="img" aria-label="Dark timber country home at dusk with a gravel path"></div>
      <div class="brand" style="top:110px"><p class="brand-name">MARA LINWOOD</p><p class="brand-role">PHOTOGRAPHER</p></div>
      <p class="welcome">Welcome to the</p>
      <h1 class="title-big">KTR</h1>
      <p class="title-sub">REAL ESTATE<br>PHOTOGRAPHY</p>
      <div class="black-band"></div>
      <p class="band-text">EDITING AND<br>SUPPORT SERVICE</p>
      <div class="accent-right"></div><div class="gallery-frame"></div>
      <div class="g1 photo" role="img" aria-label="Modern farmhouse exterior at dusk"></div>
      <div class="g2 photo" role="img" aria-label="Timber-ceiling living room with large windows"></div>
      <div class="g3 photo" role="img" aria-label="Gallery hallway with framed art"></div>
      <div class="how-head">HOW IT WORKS</div>
      <ol class="how-box">
        <li><span class="num">01</span><span>We understand that your time is valuable, so let us handle the editing and delivery of your images. You shoot, and we take care of the rest.</span></li>
        <li><span class="num">02</span><span>Images are edited and delivered within 1 working day</span></li>
      </ol>
      <div class="foot-grey"></div><div class="foot-black"></div>
      <div class="portrait" role="img" aria-label="Portrait of the photographer"></div>
      <p class="foot-name">MARA LINWOOD<br>PHOTOGRAPHY</p>
      <div class="foot-contact"><p class="phone">61 400 555 019</p><p class="mail">shoot@maralinwood.com.au</p></div>
    </article>
  </div>
  <div class="thumb thumb--back">
    <article class="flyer">
      <div class="back-hero photo" role="img" aria-label="Coastal cliffs at sunrise beside a dark modern cabin"></div>
      <div class="brand back-brand"><p class="brand-name">MARA LINWOOD</p><p class="brand-role">PHOTOGRAPHER</p></div>
      <div class="inc-head">INCLUSIONS</div>
      <div class="inc-body"></div>
      <div class="b1 photo" role="img" aria-label="Bright dining kitchen"></div>
      <div class="b2 photo" role="img" aria-label="Dark lounge with sofa"></div>
      <div class="b3 photo" role="img" aria-label="Bedroom with valley view"></div>
      <p class="inv-title">INVESTMENT</p>
      <div class="foot-grey"></div><div class="foot-black"></div>
      <div class="portrait" role="img" aria-label="Portrait of the photographer"></div>
      <p class="foot-name">MARA LINWOOD<br>PHOTOGRAPHY</p>
      <div class="foot-contact"><p class="phone">61 400 555 019</p><p class="mail">shoot@maralinwood.com.au</p></div>
    </article>
  </div>
</section>

<!-- Front side -->
<div class="sheet sheet--front">
  <article class="flyer">
    <div class="accent-top"></div>
    <div class="accent-side"></div>
    <div class="hero-frame"></div>
    <div class="hero-photo photo" role="img" aria-label="Dark timber country home at dusk with a gravel path and lawn"></div>
    <div class="brand" style="top:110px"><p class="brand-name">MARA LINWOOD</p><p class="brand-role">PHOTOGRAPHER</p></div>
    <p class="welcome">Welcome to the</p>
    <h1 class="title-big">KTR</h1>
    <p class="title-sub">REAL ESTATE<br>PHOTOGRAPHY</p>
    <div class="black-band"></div>
    <p class="band-text">EDITING AND<br>SUPPORT SERVICE</p>
    <div class="accent-right"></div>
    <div class="gallery-frame"></div>
    <div class="g1 photo" role="img" aria-label="Modern stone and white farmhouse exterior at dusk"></div>
    <div class="g2 photo" role="img" aria-label="Living room with timber ceiling and floor-to-ceiling windows"></div>
    <div class="g3 photo" role="img" aria-label="Bright hallway lined with framed artwork"></div>

    <ul class="benefits">
      <li><span class="icon"><svg viewBox="0 0 28 28"><path d="M4 22 14 5l10 17z" fill="none" stroke="#fff" stroke-width="2"/><path d="M10 22v-6h8v6" fill="none" stroke="#fff" stroke-width="2"/></svg></span><span>Take your real estate business to the next level by providing impressive real estate imagery that makes you stands out from the competition</span></li>
      <li><span class="icon"><svg viewBox="0 0 28 28"><rect x="3" y="8" width="22" height="15" rx="2" fill="none" stroke="#fff" stroke-width="2"/><circle cx="14" cy="15.5" r="4.5" fill="none" stroke="#fff" stroke-width="2"/><rect x="10" y="5" width="8" height="3" fill="#fff"/></svg></span><span>Omit the stress of trying to find a good photographer or managing an unreliable one and hence have more time to focus on other aspects of your business</span></li>
      <li><span class="icon"><svg viewBox="0 0 28 28"><circle cx="14" cy="14" r="10" fill="none" stroke="#fff" stroke-width="2"/><path d="M9 19 19 9" stroke="#fff" stroke-width="2"/><circle cx="10" cy="10" r="2" fill="#fff"/><circle cx="18" cy="18" r="2" fill="#fff"/></svg></span><span>Showcase your listings with better quality and more impactful photographs than your competitors there by increasing potential for a quick sale</span></li>
      <li><span class="icon"><svg viewBox="0 0 28 28"><circle cx="14" cy="9" r="3.5" fill="#fff"/><circle cx="6" cy="11" r="2.5" fill="#fff"/><circle cx="22" cy="11" r="2.5" fill="#fff"/><path d="M8 23c0-5 3-8 6-8s6 3 6 8zM2 22c0-4 2-6 4-6s3 1 3 2M26 22c0-4-2-6-4-6s-3 1-3 2" fill="#fff"/></svg></span><span>Great first impressions matter and you will achieve this by looking and feeling more professional. This will attract and retain more future clients.</span></li>
    </ul>

    <div class="how-head">HOW IT WORKS</div>
    <ol class="how-box">
      <li><span class="num">01</span><span>We understand that your time is valuable, so let us handle the editing and delivery of your images. You shoot, and we take care of the rest.</span></li>
      <li><span class="num">02</span><span>Images are edited and delivered within 1 working day</span></li>
    </ol>

    <div class="foot-grey"></div>
    <div class="foot-black"></div>
    <div class="portrait" role="img" aria-label="Portrait of the photographer"></div>
    <p class="foot-name">MARA LINWOOD<br>PHOTOGRAPHY</p>
    <div class="foot-contact">
      <p class="phone"><svg class="cicon" viewBox="0 0 22 22"><circle cx="11" cy="11" r="11" fill="#fff"/><path d="M7 5.5l2.2 2.6-1.2 1.6a8 8 0 0 0 4.3 4.3l1.6-1.2 2.6 2.2-1.3 1.8C10 16.5 5.5 12 5.2 6.8z" fill="#000"/></svg>61 400 555 019</p>
      <p class="mail"><svg class="cicon" viewBox="0 0 22 22"><circle cx="11" cy="11" r="11" fill="#fff"/><rect x="5" y="7" width="12" height="9" fill="#000"/><path d="M5 7l6 5 6-5" fill="none" stroke="#fff" stroke-width="1.2"/></svg>shoot@maralinwood.com.au</p>
    </div>
  </article>
</div>

<!-- Back side -->
<div class="sheet sheet--back">
  <article class="flyer">
    <div class="back-hero photo" role="img" aria-label="Coastal cliffs and ocean at sunrise beside a dark clad modern cabin"></div>
    <div class="brand back-brand"><p class="brand-name">MARA LINWOOD</p><p class="brand-role">PHOTOGRAPHER</p></div>

    <div class="inc-head">INCLUSIONS</div>
    <ul class="inc-body">
      <li><span class="icon"><svg viewBox="0 0 28 28"><rect x="4" y="4" width="20" height="12" fill="none" stroke="#fff" stroke-width="2"/><circle cx="8" cy="20" r="2.5" fill="#fff"/><circle cx="14" cy="20" r="2.5" fill="#fff"/><circle cx="20" cy="20" r="2.5" fill="#fff"/></svg></span><span>Full day face to face training (we come to you) and instructional handbook</span></li>
      <li><span class="icon"><svg viewBox="0 0 28 28"><circle cx="14" cy="7" r="3.5" fill="#fff"/><path d="M4 17l10 4 10-4v5l-10 4-10-4z" fill="#fff"/></svg></span><span>We will teach you everything you need to know about your equipment and how to take stunning real estate photographs</span></li>
      <li><span class="icon"><svg viewBox="0 0 28 28"><circle cx="9" cy="6" r="3" fill="#fff"/><path d="M6 12h6v6l-3 8M9 18l-3 8" stroke="#fff" stroke-width="2.5" fill="none"/><path d="M20 8v18M16 26l4-8 4 8" stroke="#fff" stroke-width="2" fill="none"/></svg></span><span>Service turnaround within 1 working day</span></li>
      <li><span class="icon"><svg viewBox="0 0 28 28"><circle cx="14" cy="10" r="5" fill="#fff"/><path d="M5 25c0-6 4-9 9-9s9 3 9 9z" fill="#fff"/></svg></span><span class="strong">Free HELP desk service<br>MON-FRI</span></li>
      <li><span class="icon"><svg viewBox="0 0 28 28"><circle cx="14" cy="11" r="7" fill="none" stroke="#fff" stroke-width="2"/><circle cx="14" cy="11" r="3" fill="#fff"/><path d="M9 17l-2 8 7-3 7 3-2-8" fill="#fff"/></svg></span><span><span class="strong">12 MONTH</span><small>Exclusivity (rural towns only)<br>for a limited time</small></span></li>
    </ul>

    <div class="b1 photo" role="img" aria-label="Bright open plan dining room and kitchen"></div>
    <div class="b2 photo" role="img" aria-label="Dark styled lounge with sofa and cushions"></div>
    <div class="b3 photo" role="img" aria-label="Light bedroom with large windows onto the valley"></div>

    <p class="inv-title">INVESTMENT</p>
    <ul class="inv-list">
      <li><svg class="tick" viewBox="0 0 17 17"><circle cx="8.5" cy="8.5" r="8.5" fill="#111"/><path d="M4.5 8.8l2.6 2.6 5.3-5.6" fill="none" stroke="#fff" stroke-width="1.8"/></svg><span>99 per listing for us to manage images <b>including editing, quality control and delivery (10 IMAGES)</b></span></li>
      <li><svg class="tick" viewBox="0 0 17 17"><circle cx="8.5" cy="8.5" r="8.5" fill="#111"/><path d="M4.5 8.8l2.6 2.6 5.3-5.6" fill="none" stroke="#fff" stroke-width="1.8"/></svg><b>Ask us about competitive packages for photography equipment if required</b></li>
    </ul>

    <div class="foot-grey"></div>
    <div class="foot-black"></div>
    <div class="portrait" role="img" aria-label="Portrait of the photographer"></div>
    <p class="foot-name">MARA LINWOOD<br>PHOTOGRAPHY</p>
    <div class="foot-contact">
      <p class="phone"><svg class="cicon" viewBox="0 0 22 22"><circle cx="11" cy="11" r="11" fill="#fff"/><path d="M7 5.5l2.2 2.6-1.2 1.6a8 8 0 0 0 4.3 4.3l1.6-1.2 2.6 2.2-1.3 1.8C10 16.5 5.5 12 5.2 6.8z" fill="#000"/></svg>61 400 555 019</p>
      <p class="mail"><svg class="cicon" viewBox="0 0 22 22"><circle cx="11" cy="11" r="11" fill="#fff"/><rect x="5" y="7" width="12" height="9" fill="#000"/><path d="M5 7l6 5 6-5" fill="none" stroke="#fff" stroke-width="1.2"/></svg>shoot@maralinwood.com.au</p>
    </div>
  </article>
</div>

</body>
</html>
```